Business Card Update, need to bring life to the card, two sided color

We need a new business card design, are moving and changing addresses and need a new look, we have the logos already attached but need a new style moving forward. Can incorporate the color of the logo (The Green) as well, maybe a solid back? We deal with safety products revolving around static electricity and safety lighting. Would like to keep same font in second logo as well.

Target Market(s)

Electrical Safety, Lighting

Contact Information for Business Card

Dale Fenwick
Vice President
Office: 770-555-4821
Cell: 770-555-3067
dale@tkfenwick.example
www.tkfenwick.example
4700 West Harbor Boulevard
Suite #150
Roswell, GA 30076

Font styles to use
Serif
Sans Serif

Requirements
Must have
• Since 1918
Nice to have
• Could use the 100 Year Logo for back of card, would like the back of card to be the same green as logo.
Should not have
• No black cards please.

```html
<!DOCTYPE html>
<html lang="en">
<head>
<meta charset="utf-8">
<title>Tallis K. Fenwick – Business Card</title>
<link rel="stylesheet" href="https://fonts.googleapis.com/css2?family=Arimo:wght@700&family=Open+Sans:wght@400&display=swap">
<style>
  :root {
    --brand-green: #009a5a;
    --ink: #000000;
    --paper: #ffffff;
    --backdrop: #eef2f0;
    --frame: #1a1a1a;
    --title-ink: #222222;
  }
  html, body {
    margin: 0;
    padding: 0;
    width: 1200px;
    height: 1007px;
    overflow: hidden;
    background: var(--backdrop);
  }
  .stage {
    position: absolute;
    left: 0;
    top: 0;
    width: 1317px;
    height: 1105px;
    box-sizing: border-box;
    border: 3px solid var(--frame);
    background: var(--backdrop);
    transform: scale(0.9112);
    transform-origin: 0 0;
  }
  .card {
    position: absolute;
    overflow: hidden;
  }
  .card-front {
    left: 58px;
    top: 50px;
    width: 848px;
    height: 485px;
    border-radius: 36px;
    background: var(--paper);
    border: 1px solid #333;
    box-sizing: border-box;
  }
  .card-back {
    left: 343px;
    top: 553px;
    width: 894px;
    height: 510px;
    border-radius: 28px;
    background: var(--brand-green);
  }
  .front-shapes {
    position: absolute;
    left: 0;
    top: 0;
    width: 848px;
    height: 485px;
  }
  .brand-mark {
    position: absolute;
    border-radius: 50%;
  }
  .front-mark {
    left: 38px;
    top: 36px;
    width: 140px;
    height: 140px;
    background: var(--brand-green);
  }
  .brand-name {
    position: absolute;
    margin: 0;
    font-family: "Arimo", Arial, sans-serif;
    font-weight: 700;
    color: var(--brand-green);
    white-space: nowrap;
    line-height: 1;
  }
  .front-brand {
    left: 191px;
    top: 72px;
  }
  .front-brand .brand-primary { font-size: 44px; display: block; }
  .front-brand .brand-secondary { font-size: 22px; display: block; margin-top: 6px; margin-left: 28px; letter-spacing: 0.5px; }
  .front-brand .brand-since { font-size: 16px; display: block; margin-top: 8px; margin-left: 28px; letter-spacing: 2px; text-transform: uppercase; }
  .person {
    position: absolute;
    left: 44px;
    top: 284px;
    font-family: "Arimo", Arial, sans-serif;
    font-weight: 700;
  }
  .person-name { margin: 0; font-size: 33px; color: var(--brand-green); line-height: 1.05; }
  .person-title { margin: 2px 0 0; font-size: 25px; color: var(--title-ink); line-height: 1.1; }
  .contact-list {
    position: absolute;
    right: 12px;
    top: 292px;
    margin: 0;
    padding: 0;
    list-style: none;
    font-family: "Open Sans", Arial, sans-serif;
    font-size: 18px;
    color: var(--paper);
    text-align: right;
  }
  .contact-item {
    display: flex;
    justify-content: flex-end;
    align-items: center;
    gap: 8px;
    height: 26px;
  }
  .contact-item svg { width: 17px; height: 17px; flex: none; }
  .contact-address { line-height: 23px; margin-top: 2px; padding-right: 25px; }
  .back-mark {
    left: 312px;
    top: 30px;
    width: 270px;
    height: 270px;
    background: var(--paper);
  }
  .back-brand {
    left: 0;
    width: 894px;
    top: 322px;
    text-align: center;
    color: var(--paper);
  }
  .back-brand .brand-primary { font-size: 45px; display: block; }
  .back-brand .brand-secondary { font-size: 22px; display: block; margin-top: 6px; letter-spacing: 0.5px; }
  .back-brand .brand-since { font-size: 18px; display: block; margin-top: 12px; letter-spacing: 3px; text-transform: uppercase; }
  .back-web {
    position: absolute;
    left: 0;
    width: 894px;
    top: 458px;
    margin: 0;
    text-align: center;
    font-family: "Open Sans", Arial, sans-serif;
    font-size: 27px;
    letter-spacing: 6px;
    color: var(--paper);
  }
</style>
</head>
<body>
<div class="stage">

  <section class="card card-front" aria-label="Business card front">
    <svg class="front-shapes" viewBox="0 0 848 485" aria-hidden="true">
      <path fill="var(--brand-green)" d="M0,355 C150,420 430,400 597,268 C470,385 250,452 0,405 Z"/>
      <path fill="var(--ink)" d="M0,415 C350,500 660,300 848,20 L848,485 L0,485 Z"/>
    </svg>

    <div class="brand-mark front-mark"></div>
    <p class="brand-name front-brand">
      <span class="brand-primary">Tallis K. Fenwick</span>
      <span class="brand-secondary">Manufacturing Company, Inc.</span>
      <span class="brand-since">Since 1918</span>
    </p>

    <div class="person">
      <h1 class="person-name">Dale Fenwick</h1>
      <p class="person-title">Vice President</p>
    </div>

    <ul class="contact-list">
      <li class="contact-item">Office 770-555-4821
        <svg viewBox="0 0 20 20" aria-hidden="true"><circle cx="10" cy="10" r="8.5" fill="none" stroke="#fff" stroke-width="1.6"/><path d="M6.5 5.5 l2 0 l0.8 2.4 l-1.3 1 q1 2 3 3 l1-1.3 l2.4 0.8 l0 2 q-5 0.5 -7.9 -7.9z" fill="#fff"/></svg>
      </li>
      <li class="contact-item">Cell 770-555-3067
        <svg viewBox="0 0 20 20" aria-hidden="true"><circle cx="10" cy="10" r="8.5" fill="none" stroke="#fff" stroke-width="1.6"/><rect x="7" y="4.5" width="6" height="11" rx="1" fill="none" stroke="#fff" stroke-width="1.4"/><circle cx="10" cy="13.2" r="0.8" fill="#fff"/></svg>
      </li>
      <li class="contact-item">dale@tkfenwick.example
        <svg viewBox="0 0 20 20" aria-hidden="true"><circle cx="10" cy="10" r="8.5" fill="none" stroke="#fff" stroke-width="1.6"/><rect x="5.5" y="7" width="9" height="6.5" fill="none" stroke="#fff" stroke-width="1.4"/><path d="M5.5 7 l4.5 3.5 l4.5 -3.5" fill="none" stroke="#fff" stroke-width="1.4"/></svg>
      </li>
      <li class="contact-item">www.tkfenwick.example
        <svg viewBox="0 0 20 20" aria-hidden="true"><circle cx="10" cy="10" r="8.5" fill="none" stroke="#fff" stroke-width="1.6"/><ellipse cx="10" cy="10" rx="3.6" ry="8.5" fill="none" stroke="#fff" stroke-width="1.3"/><path d="M1.5 10 h17 M3 6 h14 M3 14 h14" stroke="#fff" stroke-width="1.3"/></svg>
      </li>
      <li class="contact-address">4700 West Harbor Boulevard<br>Suite #150<br>Roswell, GA 30076</li>
    </ul>
  </section>

  <section class="card card-back" aria-label="Business card back">
    <div class="brand-mark back-mark"></div>
    <p class="brand-name back-brand">
      <span class="brand-primary">Tallis K. Fenwick</span>
      <span class="brand-secondary">Manufacturing Company, Inc.</span>
      <span class="brand-since">Since 1918</span>
    </p>
    <p class="back-web">www.tkfenwick.example</p>
  </section>

</div>
</body>
</html>
```